Business card design Needed for new logo / Construction business, home extensions and new builds

We need a business card design using our new logo files which i will attach to this project :)

We are a small construction business specialising in home extensions, new builds and property development. We are very ambitious and would appreciate professional and elegant designs for our new business card.

Very serious about using the services on MakerQuarry and recently acquired our new logo from here :)

Please get involved, i will feedback when i can as i am very busy but can respond daily, thanks

Target Market(s)

People that want to build onto their houses, new building developments or adding too their existing property

Industry/Entity Type

Construction

Contact Information for Business Card

Renwick Tolliver Construction, Lionel Ashby (Managing Director), Tel 07822254961, email - info@renwick-tolliver, www.renwick-tolliver.co.uk

Colors

Designer to choose colors to be used in the design.

Requirements
Must have
• I like a deep grey on the back please. A lot of you have provided black from and back, try mixing things up a little. The black looks cool 😎 Thanks

```html
<!DOCTYPE html>
<html lang="en">
<head>
<meta charset="utf-8">
<title>Renwick Tolliver Construction – Business Cards</title>
<link href="https://fonts.googleapis.com/css2?family=Montserrat:wght@400;600;700&display=swap" rel="stylesheet">
<style>
  :root {
    --backdrop: #4a4a49;
    --card-front: #161616;
    --card-back: #2a2a2b;
    --gold: #e0a82e;
    --text-light: #f2f2f2;
  }
  * { box-sizing: border-box; margin: 0; padding: 0; }
  html, body {
    width: 1200px; height: 801px; overflow: hidden;
    background: var(--backdrop);
    font-family: "Montserrat", Arial, sans-serif;
  }
  .stage {
    width: 1200px; height: 801px;
    display: flex; align-items: center; justify-content: center; gap: 40px;
  }
  .card {
    width: 540px; height: 309px;
    border: 2px solid var(--gold);
    border-radius: 18px;
    position: relative;
    overflow: hidden;
  }
  /* contact side (front) */
  .card-contact {
    display: flex; align-items: stretch;
    background: var(--card-front);
  }
  .brand-panel {
    width: 270px;
    display: flex; align-items: center; justify-content: center;
    padding: 0 24px;
  }
  .divider {
    width: 1px; background: var(--gold);
    margin: 62px 0;
  }
  .contact-panel {
    flex: 1;
    display: flex; flex-direction: column; justify-content: center;
    padding: 0 22px 0 26px;
    color: var(--text-light);
  }
  .brand-name {
    display: flex; align-items: center; gap: 10px;
    color: var(--gold);
    font-weight: 600;
    text-transform: uppercase;
    letter-spacing: 0.08em;
    line-height: 1.3;
  }
  .brand-mark {
    flex: none;
    width: 14px; height: 14px;
    background: var(--gold);
  }
  .brand-panel .brand-name { font-size: 17px; }
  .person-name {
    color: var(--gold);
    font-weight: 700; font-size: 19px;
    letter-spacing: 0.02em;
    text-transform: uppercase;
  }
  .person-role { font-size: 13px; margin-top: 2px; }
  .contact-list { list-style: none; margin-top: 18px; font-size: 12.5px; }
  .contact-list li { display: flex; align-items: center; gap: 8px; margin-bottom: 5px; }
  .contact-list svg { width: 12px; height: 12px; flex: none; }
  .address { font-size: 12.5px; margin-top: 12px; line-height: 1.45; }
  /* logo side (back, deep grey) */
  .card-logo {
    display: flex; align-items: center; justify-content: center;
    background: var(--card-back);
  }
  .card-logo .brand-name { font-size: 26px; gap: 14px; }
  .card-logo .brand-mark { width: 20px; height: 20px; }
</style>
</head>
<body>
<main class="stage">
  <section class="card card-contact" aria-label="Business card, contact side">
    <div class="brand-panel">
      <p class="brand-name"><span class="brand-mark"></span><span>Renwick Tolliver<br>Construction</span></p>
    </div>
    <div class="divider"></div>
    <div class="contact-panel">
      <h1 class="person-name">Lionel Ashby</h1>
      <p class="person-role">Managing Director</p>
      <ul class="contact-list">
        <li>
          <svg viewBox="0 0 24 24" aria-hidden="true"><path fill="var(--gold)" d="M6.6 10.8a15.5 15.5 0 0 0 6.6 6.6l2.2-2.2c.3-.3.7-.4 1-.2 1.1.4 2.3.6 3.6.6.6 0 1 .4 1 1V20c0 .6-.4 1-1 1A17 17 0 0 1 3 4c0-.6.4-1 1-1h3.5c.6 0 1 .4 1 1 0 1.3.2 2.5.6 3.6.1.3 0 .7-.2 1z"/></svg>
          07822254961
        </li>
        <li>
          <svg viewBox="0 0 24 24" aria-hidden="true"><path fill="var(--gold)" d="M2 5h20v14H2z"/><path fill="none" stroke="var(--card-front)" stroke-width="2" d="M2 5l10 8 10-8"/></svg>
          info@renwick-tolliver
        </li>
        <li>
          <svg viewBox="0 0 24 24" aria-hidden="true"><circle cx="12" cy="12" r="10" fill="var(--gold)"/><path fill="none" stroke="var(--card-front)" stroke-width="1.5" d="M2 12h20M12 2c3 3 3 17 0 20M12 2c-3 3-3 17 0 20"/></svg>
          www.renwick-tolliver.co.uk
        </li>
      </ul>
      <p class="address">Your address, City<br>State, Zip 1234</p>
    </div>
  </section>

  <section class="card card-logo" aria-label="Business card, logo side">
    <p class="brand-name"><span class="brand-mark"></span><span>Renwick Tolliver<br>Construction</span></p>
  </section>
</main>
</body>
</html>
```